Kelvo bottle Label (Yoghurt drink)

Label for a 300 ml yoghurt drink bottle in 3 flavours.

General description:
• This is to design a sleeve shrink label for a Yoghurt Drink bottle in three flavours, Classic, Strawberry and Blueberry.
• Attached 3 photos: The one with KELVO brand in the current design we want to replace using the same bottle.
• Graphically, the design is to be similar to the examples provided for drumelo and fizzcrate.
• Use font and barcode size to be readable and legal.
• Minimize the use of the upper third of the bottle as it will be distorted when the label shrinks to the bottle.
• Professional and experienced designers only are welcome, please do not waste your time otherwise.

Bottle dimensions:
• Base across: 61 mm
• Height: 145 mm (approximate)

Graphical description:
• White colour with bands at the top and bottom similar to the one in “drumelo” example provided (not necessarily identical, feel free to be creative.
• The upper and lower bands to be: Green for “classic”, Pink or red for strawberry and purple for blueberry flavour.
• On the front: the brand name “Kelvo” and description “Yoghurt Drink” to be graphically attractive.
• On the front: two or more pieces of strawberry or blueberry for each flavour placed nicely with the option to include “yoghurt splash” or any suitable affects you deem suitable.
• For the Classic flavour, use the words (Classic, Lassi, Ayran) in the same location for the berries done in a graphically suitable manner.
• Colour temperature for the three flavours to be similar.

Information and objects on the label:
Front:
• The word “Kelvo” (brand name)
• “Yoghurt drink” (Product description)
• “300 ml” (size)
• Picture of Strawberries for strawberry flavour.
• Picture of Blueberries for blueberry flavour.
• The words (Classic, Lassi, Ayran) in the place used for the strawberries in the flavoured type, distributed to look graphically suitable for the overall design.

Back:
• Ingredient: Milk/milk solids, culture, salt, water, sugar, colour, flavour. (this is to be finalized later)
• Nutrition information table: (to be provided later).
• Barcode (to be provided later)
• Product of Australia
• Morel Tunsley Pty Ltd, 5/14 Ferrit St, Malaga, WA 6090
• info@kelvo-example.com.au 0491 000 372
• Keep under 5⁰ C
• Best before date printed on the bottle
• Shake well (to be located on the side at the top)
• Recycle icon.

Health benefits: (to be located suitably, possibly on the side with vertical orientation)
• Rich in probiotic bacteria and vitamins.
• Improves digestion and bowel motion.
• Supports weight control and fat loss.

Target Market(s)

General consumers

Industry/Entity Type

Grocery Store

Font styles to use
Sans Serif

Colors
abd037
b768aa
f04a50

Requirements
Must have
• The details in the project description
• The design must be simple and neat.
• Please use the shape of the current bottle "Kelvo" as in the attached photo.
Should not have
• Busy, cluttered, or empty and incomplete designs.

```html
<!DOCTYPE html>
<html lang="en">
<head>
<meta charset="utf-8">
<title>Kelvo Yoghurt Drink – Blueberry Label</title>
<link href="https://fonts.googleapis.com/css2?family=Fredoka:wght@600;700&family=Montserrat:wght@500;700&display=swap" rel="stylesheet">
<style>
  :root {
    --paper: #ffffff;
    --lilac: #a36fb0;
    --plum: #8e2a90;
    --berry: #b0208c;
    --magenta: #ec008c;
    --splash-top: #ef7d92;
    --splash-bottom: #e8602c;
    --brand: #8e2a90;
    --outline: #e4007f;
  }
  html, body {
    margin: 0;
    padding: 0;
    width: 1200px;
    height: 1126px;
    overflow: hidden;
    background: var(--paper);
  }
  .label {
    display: block;
    width: 1200px;
    height: 1126px;
  }
  .brand-name {
    font-family: "Montserrat", sans-serif;
    font-weight: 700;
    font-size: 44px;
    fill: var(--brand);
    letter-spacing: 2px;
  }
  .brand-descriptor {
    font-family: "Montserrat", sans-serif;
    font-weight: 500;
    font-size: 17px;
    fill: var(--brand);
  }
  .product-word {
    font-family: "Fredoka", sans-serif;
    font-weight: 700;
    font-size: 190px;
    fill: var(--paper);
    stroke: var(--outline);
    stroke-width: 9px;
    stroke-linejoin: round;
    paint-order: stroke;
  }
  .product-sub {
    font-family: "Fredoka", sans-serif;
    font-weight: 700;
    font-size: 72px;
    fill: var(--paper);
  }
</style>
</head>
<body>
<svg class="label" viewBox="0 0 1500 1408" xmlns="http://www.w3.org/2000/svg">
  <defs>
    <linearGradient id="splash" x1="0" y1="0" x2="0" y2="1">
      <stop offset="0" stop-color="var(--splash-top)"/>
      <stop offset="1" stop-color="var(--splash-bottom)"/>
    </linearGradient>
    <radialGradient id="berries" cx="0.45" cy="0.45" r="0.6">
      <stop offset="0" stop-color="#6f86b8"/>
      <stop offset="0.7" stop-color="#3d4f86"/>
      <stop offset="1" stop-color="#5fa83a" stop-opacity="0.85"/>
    </radialGradient>
  </defs>

  <g class="splashes">
    <path d="M420,830 C380,900 300,880 290,920 C280,960 340,970 400,940 Z" fill="url(#splash)" opacity="0.8"/>
    <path d="M440,980 C380,1020 270,1040 252,1090 C236,1140 290,1160 350,1120 C400,1090 430,1040 460,1010 Z" fill="url(#splash)"/>
    <ellipse cx="590" cy="1140" rx="110" ry="65" fill="url(#splash)" opacity="0.85"/>
    <path d="M830,800 C920,790 1060,820 1070,880 C1080,950 960,960 880,920 C840,900 820,860 830,800 Z" fill="url(#splash)"/>
    <path d="M880,960 C930,960 1000,970 998,1005 C996,1040 930,1030 890,1000 Z" fill="url(#splash)" opacity="0.85"/>
    <ellipse cx="1015" cy="1080" rx="25" ry="22" fill="#e88ab0"/>
  </g>

  <g class="ribbons">
    <path d="M350,0 C330,400 300,750 420,1000 C520,1200 640,1330 720,1408 L1010,1408 C800,1250 620,1100 560,900 C480,650 720,350 600,0 Z" fill="var(--lilac)" opacity="0.8"/>
    <path d="M420,0 C480,250 520,450 540,700 C560,950 720,1160 1120,1408 L1420,1408 C1010,1250 760,1050 690,800 C620,560 600,300 470,0 Z" fill="var(--berry)"/>
    <path d="M470,120 C560,260 610,450 630,700 C650,950 840,1160 1420,1408 L1200,1408 C850,1240 700,1050 650,820 C610,620 560,330 470,120 Z" fill="var(--magenta)"/>
    <path d="M520,900 C600,1080 760,1230 1000,1408 L1180,1408 C900,1260 700,1110 600,930 Z" fill="var(--plum)" opacity="0.9"/>
    <path d="M330,0 C380,60 420,80 470,120 L440,0 Z" fill="var(--plum)" opacity="0.7"/>
  </g>

  <g class="brand-lockup">
    <rect x="704" y="100" width="18" height="18" fill="var(--brand)"/>
    <text class="brand-name" x="788" y="122" text-anchor="middle">KELVO</text>
    <text class="brand-descriptor" x="778" y="160" text-anchor="middle">ACTIVE YOGHURT</text>
    <text class="brand-descriptor" x="778" y="182" text-anchor="middle">DRINK</text>
  </g>

  <path class="berry-cluster" role="img" aria-label="Four fresh blueberries with green leaves"
        d="M600,520 C650,470 740,480 800,520 C880,560 980,580 1010,630 C990,700 930,760 870,790 C860,880 780,920 700,900 C630,880 600,820 590,760 C560,700 560,580 600,520 Z"
        fill="url(#berries)"/>

  <text class="product-word" x="600" y="820" text-anchor="middle" transform="rotate(58.6 600 760)">Yogurt</text>
  <text class="product-sub" x="585" y="1020" text-anchor="middle" transform="rotate(58.6 585 995)">Drink</text>
</svg>
</body>
</html>
```